Indy Film Production Company/Studio

We need a business card designed from an existing logo. We are a digital studio/production company that caters to creating genre entertainment, like Action, Horror, and martial arts. The card along with the logo will be used to Brand the company from letter heads to banners. The design will also be used for postcards and Brochures. It should be professional and masculine.
Updates

Thank you to all the designers who have participated. I'm narrowing down who it will be. Thank you again.

Target Market(s)

Investors, Networks, Producers, and actors

Industry/Entity Type

Film Production

Contact Information for Business Card

Teodoro Valbuena
Producer/Writer/Director
www.kestrelpicturehouse.example

Requirements
Must have
• Website address, Facebook icon and Twitter icon possibly in the back of the card.
Nice to have
• Logline of Company: Follow The Action.

```html
<!DOCTYPE html>
<html lang="en">
<head>
<meta charset="utf-8">
<title>Kestrel Picture House — Business Card</title>
<link rel="stylesheet" href="https://fonts.googleapis.com/css2?family=Open+Sans:wght@400;600;800&display=swap">
<style>
  :root {
    --page: #e7e5e2;
    --card: #121212;
    --card-edge: #1d1d1d;
    --text: #e9e9e9;
    --muted: #b9b9b9;
    --accent: #e0262b;
    --photo-a: #3a3a3a;
    --photo-b: #0c0c0c;
    --social: #4a4a4a;
  }
  * { box-sizing: border-box; margin: 0; padding: 0; }
  html, body { width: 1200px; height: 814px; overflow: hidden; }
  body {
    background: var(--page);
    font-family: "Open Sans", Arial, sans-serif;
    position: relative;
  }
  .card {
    position: absolute;
    top: 252px;
    width: 540px;
    height: 310px;
    background: var(--card);
    border: 1px solid var(--card-edge);
    box-shadow: 0 6px 18px rgba(0,0,0,.25);
    overflow: hidden;
  }
  .card--front { left: 40px; }
  .card--back { left: 620px; }

  .equipment-photo {
    position: absolute;
    left: 170px;
    top: 16px;
    width: 340px;
    height: 124px;
    border-radius: 6px;
    background: radial-gradient(ellipse at 45% 50%, var(--photo-a), var(--photo-b) 75%);
  }
  .contact {
    position: absolute;
    left: 34px;
    bottom: 28px;
    color: var(--text);
  }
  .contact__name {
    color: var(--accent);
    font-size: 21px;
    font-weight: 400;
    line-height: 1.2;
  }
  .contact__role {
    font-size: 15px;
    line-height: 1.4;
    margin-bottom: 8px;
  }
  .contact__line {
    display: flex;
    align-items: center;
    gap: 10px;
    font-size: 14px;
    line-height: 1.75;
  }
  .contact__line svg { width: 13px; height: 13px; fill: var(--accent); flex: none; }

  .brand {
    position: absolute;
    left: 0; right: 0;
    top: 112px;
    text-align: center;
    color: var(--text);
  }
  .brand__initials {
    font-size: 56px;
    font-weight: 800;
    letter-spacing: 2px;
    line-height: 1;
  }
  .brand__name {
    font-size: 17px;
    font-weight: 800;
    letter-spacing: 1px;
    text-transform: uppercase;
    margin-top: 4px;
  }
  .brand__web {
    font-size: 12px;
    color: var(--muted);
    letter-spacing: 2px;
    margin-top: 4px;
  }
  .social {
    position: absolute;
    top: 14px;
    right: 16px;
    display: flex;
    gap: 5px;
  }
  .social__slot {
    width: 14px; height: 14px;
    background: var(--social);
    border-radius: 2px;
  }
</style>
</head>
<body>
  <section class="card card--front" aria-label="Card front">
    <div class="equipment-photo" role="img" aria-label="Photograph of a cinema camera rig on a jib arm"></div>
    <div class="contact">
      <p class="contact__name">Teodoro Valbuena</p>
      <p class="contact__role">Producer/Writer/Director</p>
      <p class="contact__line">
        <svg viewBox="0 0 24 24" aria-hidden="true"><path d="M6.6 10.8a15 15 0 0 0 6.6 6.6l2.2-2.2a1 1 0 0 1 1-.25 11.4 11.4 0 0 0 3.6.57 1 1 0 0 1 1 1V20a1 1 0 0 1-1 1A17 17 0 0 1 3 4a1 1 0 0 1 1-1h3.5a1 1 0 0 1 1 1c0 1.25.2 2.45.57 3.6a1 1 0 0 1-.25 1z"/></svg>
        555 014 2290
      </p>
      <p class="contact__line">
        <svg viewBox="0 0 24 24" aria-hidden="true"><path d="M2 5h20v14H2z M3 6l9 7 9-7"/></svg>
        hello@kestrelpicturehouse.example
      </p>
      <p class="contact__line">
        <svg viewBox="0 0 24 24" aria-hidden="true"><circle cx="12" cy="12" r="10"/></svg>
        www.kestrelpicturehouse.example
      </p>
    </div>
  </section>

  <section class="card card--back" aria-label="Card back">
    <div class="social" role="img" aria-label="Social network badges">
      <span class="social__slot"></span><span class="social__slot"></span>
    </div>
    <div class="brand">
      <p class="brand__initials">KPH</p>
      <p class="brand__name">Kestrel Picture House</p>
      <p class="brand__web">www.kestrelpicturehouse.example</p>
    </div>
  </section>
</body>
</html>
```